Veltrane Group Business Card Design

The CEO is looking for a new trendy look for his business card.
You can stay with current branding or come up with something new/creative. It can be 3D, including Medical Office buildings. You can use our logo in a variety of colors. Please include name, title, company name, company website, email address, cell number

Target Market(s)

Real Estate Development and Construction

Industry/Entity Type

Health care real estate

Contact Information for Business Card

Rohesh Kamdar, CEO M-604.781.2249 E-roheshkamdar@veltrane.com Address:4180 Lindqvist Ave, Tampa, FL 33482 www.veltrane.com

Font styles to use
Other font styles liked:
• Be creative

Requirements
Must have
• Creative, trendy look
Nice to have
• Please go to our website to get a feel- www. veltrane.com
Should not have
• small fonts

```html
<!DOCTYPE html>
<html lang="en">
<head>
<meta charset="utf-8">
<title>Veltrane Group Business Card</title>
<link rel="stylesheet" href="https://fonts.googleapis.com/css2?family=Montserrat:wght@400;700;800&display=swap">
<style>
:root{
  --stage:#3b3b3b;
  --card-dark:#141414;
  --mark-dark:#262626;
  --card-light:#ffffff;
  --ink:#0d0d0d;
  --rule:#1a1a1a;
}
*{margin:0;padding:0;box-sizing:border-box}
html,body{width:1200px;height:875px;overflow:hidden}
body{background:var(--stage);font-family:"Montserrat",sans-serif;position:relative}
.card{position:absolute;left:250px;width:700px;height:400px;border-radius:24px}
.card--back{top:25px;background:var(--card-dark)}
.card--front{top:450px;background:var(--card-light);color:var(--ink)}
.brand{position:absolute;font-weight:800;letter-spacing:-2px;line-height:1;white-space:nowrap}
.card--back .brand{left:0;right:0;top:165px;text-align:center;font-size:72px;color:var(--mark-dark)}
.card--front .brand{left:0;right:0;top:60px;text-align:center;font-size:68px;color:var(--ink)}
.identity{position:absolute;right:375px;top:200px;text-align:right}
.identity__name{font-weight:700;font-size:26px;white-space:nowrap}
.identity__title{font-weight:400;font-size:16px;margin-top:4px}
.divider{position:absolute;left:340px;top:188px;width:2px;height:96px;background:var(--rule)}
.contacts{position:absolute;left:360px;top:186px;list-style:none}
.contacts li{display:flex;align-items:center;gap:10px;font-size:16px;height:33px;white-space:nowrap}
.contacts svg{width:16px;height:16px;flex:none}
.address{position:absolute;left:0;right:0;top:322px;text-align:center;font-size:16px}
</style>
</head>
<body>
  <section class="card card--back" aria-label="Card back">
    <div class="brand">Veltrane Group</div>
  </section>

  <section class="card card--front" aria-label="Card front">
    <div class="brand">Veltrane Group</div>
    <div class="identity">
      <div class="identity__name">Rohesh Kamdar</div>
      <div class="identity__title">CEO</div>
    </div>
    <div class="divider"></div>
    <ul class="contacts">
      <li>
        <svg viewBox="0 0 16 16" aria-hidden="true"><path fill="currentColor" d="M4 1.5l2.2 3-1.3 1.6a8.5 8.5 0 0 0 5 5l1.6-1.3 3 2.2-1 2.3C8 15 1 8 1.7 2.5z"/></svg>
        604.781.2249
      </li>
      <li>
        <svg viewBox="0 0 16 16" aria-hidden="true"><rect x="1" y="3" width="14" height="10" rx="1" fill="currentColor"/><path d="M1.5 3.8L8 9l6.5-5.2" fill="none" stroke="#fff" stroke-width="1.3"/></svg>
        roheshkamdar@veltrane.com
      </li>
      <li>
        <svg viewBox="0 0 16 16" aria-hidden="true"><circle cx="8" cy="8" r="7" fill="currentColor"/><path d="M1 8h14M8 1c-3 3.5-3 10.5 0 14M8 1c3 3.5 3 10.5 0 14" fill="none" stroke="#fff" stroke-width="1"/></svg>
        www.veltrane.com
      </li>
    </ul>
    <div class="address">4180 Lindqvist Ave, Tampa, FL 33482</div>
  </section>
</body>
</html>
```